Bramwell IT Services Business Card

Bramwell IT Services are a Perth based IT Services company. We would like to incorporate our company logo (attached) and stick with the blue that is in that design. I would like a clean look design that isn't too busy, yet creates a lasting image that is instantly recognisable in the recipients mind.

Target Market(s)

The target audience is small/medium business owners.

Industry/Entity Type

Business

Font styles to use
Serif
Sans Serif

Colors

Designer to choose colors to be used in the design.

Requirements
Must have
• The design should include:
Business name: Bramwell IT Services
Directors Name: Marcus Tenley
Phone Number: 0483 562 904
Email: support@bramwellit.com.au
Website: www.bramwellit.com.au

```html
<!DOCTYPE html>
<html lang="en">
<head>
<meta charset="utf-8">
<title>Bramwell IT Services – Business Card</title>
<link rel="stylesheet" href="https://fonts.googleapis.com/css2?family=Didact+Gothic&family=Montserrat:wght@600;700&display=swap">
<style>
  :root {
    --page-bg: #e4e6e9;
    --card-bg: #f4f4f5;
    --brand-blue: #1a6fd1;
    --band-blue: #0f9be6;
    --text-dark: #2b2b2b;
    --text-white: #ffffff;
  }
  * { margin: 0; padding: 0; box-sizing: border-box; }
  html, body {
    width: 1200px; height: 900px; overflow: hidden;
    background: var(--page-bg);
  }
  .canvas {
    width: 1200px; height: 900px;
    display: flex; flex-direction: column;
    align-items: center; justify-content: center; gap: 40px;
  }
  .card {
    position: relative;
    width: 700px; height: 400px;
    background: var(--card-bg);
    box-shadow: 0 6px 18px rgba(0,0,0,0.12);
    overflow: hidden;
  }
  .brand {
    display: flex; align-items: center; gap: 12px;
    font-family: "Montserrat", sans-serif;
    font-weight: 700;
    color: var(--brand-blue);
    letter-spacing: 0.5px;
  }
  .brand-mark {
    display: block; border-radius: 50%;
    background: var(--brand-blue);
  }
  /* back card */
  .card-back .brand {
    position: absolute; left: 50%; top: 50%;
    transform: translate(-50%, -50%);
    font-size: 30px; white-space: nowrap;
  }
  .card-back .brand-mark { width: 34px; height: 34px; }
  /* front card */
  .card-front .brand {
    position: absolute; left: 70px; top: 70px;
    font-size: 21px; white-space: nowrap;
  }
  .card-front .brand-mark { width: 24px; height: 24px; }
  .name-band {
    position: absolute; left: 330px; right: 0; top: 170px;
    height: 48px;
    background: var(--band-blue);
    border-radius: 6px 0 0 6px;
    display: flex; align-items: center; padding-left: 28px;
  }
  .name-band h1 {
    font-family: "Montserrat", sans-serif;
    font-weight: 600; font-size: 24px;
    color: var(--text-white);
  }
  .contact-list {
    position: absolute; left: 300px; top: 240px;
    list-style: none;
    font-family: "Didact Gothic", sans-serif;
    font-size: 19px; color: var(--text-dark);
    line-height: 32px;
  }
  .contact-list li { display: flex; gap: 18px; }
  .contact-label {
    width: 14px;
    font-family: "Montserrat", sans-serif;
    font-weight: 700; font-size: 14px;
    color: var(--band-blue);
  }
</style>
</head>
<body>
<main class="canvas">
  <section class="card card-back" aria-label="Card back">
    <div class="brand"><span class="brand-mark"></span>Bramwell IT Services</div>
  </section>

  <section class="card card-front" aria-label="Card front">
    <div class="brand"><span class="brand-mark"></span>Bramwell IT Services</div>
    <div class="name-band"><h1>Marcus Tenley</h1></div>
    <ul class="contact-list">
      <li><span class="contact-label">P</span>0483 562 904</li>
      <li><span class="contact-label">E</span>support@bramwellit.com.au</li>
      <li><span class="contact-label">W</span>www.bramwellit.com.au</li>
    </ul>
  </section>
</main>
</body>
</html>
```